Yacht, Boats, Watersports company needs a redesign of business card

Hello Designers!
We are a Boat dealership company that sells fun in the water, we sell boats, Yachts, Kayaks and also yacht WaterSport toys. We are looking to redesign our business cards in to something a little bit more sophisticated. in a way that we can make better use of our company colors. I'm attaching a zipped file containing the company 3 sets of company logo which one is an horizontal another one is a vertical and also a chromed 3d logo. Also is included two set of business cards that we use and also some designs that i think it's interesting. We use PMS 2026c Orange and PMS 7687C Blue. I would like to see at least two different options with the orange as accent and also using blue as an accent color. It's really important for the business cards to have a font option and size that is legible to most people. Our current website is wwww.coralpennant.com. Please visit if you want to have a better feeling of the Boat dealership
You can send Single sided or double side options. We are now using single sided but we may be open for a double side option if we really like the design.
Target Market(s)
Marine, boat sales, yacht sales, water toys sales/
Contact Information for Business Card
Name: Dale Whitcombe
Address: 212 North Fenwick Lane,
Dania Beach, FL 33004
Phone: 954-731-8842
Fax: 954:731-8843
Cell: 954-382-1490
Email: dw@coralpennant.com
Website: coralpennant.com
Requirements
Must have
- the current information of the business card provided.
logo
use the PMS Colors
Nice to have
- a touch of elegance and sophistication but simple
Should not have
- should not have any typography that is hard to read, the card should be simple but yet sophisticated.

```html
<!DOCTYPE html>
<html lang="en">
<head>
<meta charset="utf-8">
<title>Coral Pennant Marine Center – Business Card</title>
<link href="https://fonts.googleapis.com/css2?family=Poppins:wght@400;500;600&display=swap" rel="stylesheet">
<style>
  :root {
    --brand-blue: #1f64ad;
    --brand-blue-dark: #1a5aa3;
    --brand-blue-light: #3a88c8;
    --brand-orange: #f0953a;
    --paper: #ffffff;
    --backdrop: #d9d9d9;
    --ink-light: #ffffff;
  }
  * { box-sizing: border-box; margin: 0; padding: 0; }
  html, body { width: 1200px; height: 1200px; overflow: hidden; }
  body {
    background: var(--backdrop);
    font-family: "Poppins", sans-serif;
    position: relative;
  }
  .card {
    position: absolute;
    left: 262px;
    width: 686px;
    height: 392px;
    border-radius: 20px;
    overflow: hidden;
  }
  .card--front { top: 165px; background: var(--paper); }
  .card--back {
    top: 653px;
    background: linear-gradient(200deg, var(--brand-blue-light) 0%, var(--brand-blue-dark) 100%);
  }

  /* front: brand block */
  .brand {
    position: absolute;
    left: 0; right: 0; top: 58px;
    display: flex;
    align-items: center;
    justify-content: center;
    gap: 14px;
  }
  .brand__dot {
    width: 38px; height: 38px;
    border-radius: 50%;
    background: var(--brand-orange);
  }
  .brand__name {
    color: var(--brand-blue);
    font-weight: 600;
    font-size: 26px;
    letter-spacing: 0.5px;
    text-transform: uppercase;
    line-height: 1.2;
    text-align: left;
  }

  /* front: info bands */
  .band {
    position: absolute;
    top: 236px;
    height: 108px;
    color: var(--ink-light);
  }
  .band--identity {
    left: 0; width: 340px;
    background: var(--brand-blue);
    text-align: right;
    padding: 12px 20px 0 0;
  }
  .band--contact {
    left: 344px; right: 0;
    background: var(--brand-orange);
    padding: 14px 0 0 22px;
  }
  .identity__name {
    font-weight: 600;
    font-size: 22px;
    line-height: 1.2;
    text-transform: uppercase;
  }
  .identity__line {
    font-size: 16px;
    line-height: 1.22;
  }
  .contact__row {
    display: flex;
    align-items: center;
    gap: 10px;
    font-size: 16px;
    line-height: 1.22;
  }
  .contact__icon { width: 13px; height: 13px; flex: none; fill: var(--ink-light); }

  /* back */
  .back__mark {
    position: absolute;
    left: 50%; top: 187px;
    width: 230px; height: 230px;
    margin: -115px 0 0 -115px;
    border-radius: 50%;
    border: 14px solid #0f3f78;
    display: flex;
    align-items: center;
    justify-content: center;
    text-align: center;
  }
  .back__name {
    color: #0f3f78;
    font-weight: 600;
    font-size: 24px;
    line-height: 1.2;
    text-transform: uppercase;
  }
  .back__web {
    position: absolute;
    left: 0; right: 0; top: 343px;
    text-align: center;
    color: var(--ink-light);
    font-size: 15px;
    letter-spacing: 4px;
  }
</style>
</head>
<body>

<section class="card card--front">
  <div class="brand">
    <span class="brand__dot"></span>
    <div class="brand__name">Coral Pennant<br>Marine Center</div>
  </div>

  <div class="band band--identity">
    <p class="identity__name">Dale Whitcombe</p>
    <p class="identity__line">212 North Fenwick Lane</p>
    <p class="identity__line">Dania Beach, FL 33004</p>
    <p class="identity__line">www.coralpennant.com</p>
  </div>

  <div class="band band--contact">
    <p class="contact__row">
      <svg class="contact__icon" viewBox="0 0 16 16" aria-hidden="true"><path d="M3.5 1l2.5 3-1.5 2c1 2 3 4 5 5l2-1.5 3 2.5-1.5 2.5C7 15 1 9 1 2.5z"/></svg>
      954-731-8842
    </p>
    <p class="contact__row">
      <svg class="contact__icon" viewBox="0 0 16 16" aria-hidden="true"><path d="M4 0h8v16H4zM5.5 2v10h5V2z"/></svg>
      954-382-1490
    </p>
    <p class="contact__row">
      <svg class="contact__icon" viewBox="0 0 16 16" aria-hidden="true"><path d="M4 1h7v4H4zM1 6h14v6H1zM4 10h8v5H4z"/></svg>
      954-731-8843
    </p>
    <p class="contact__row">
      <svg class="contact__icon" viewBox="0 0 16 16" aria-hidden="true"><path d="M1 4h14v9H1zM2 5l6 4 6-4v1L8 10 2 6z" fill-rule="evenodd"/></svg>
      dw@coralpennant.com
    </p>
  </div>
</section>

<section class="card card--back">
  <div class="back__mark">
    <span class="back__name">Coral<br>Pennant</span>
  </div>
  <p class="back__web">WWW.CORALPENNANT.COM</p>
</section>

</body>
</html>
```